Webdesign für Heilpraktiker
Zielgruppe
Ich bin Heilpraktiker und betreibe eine Naturheilpraxis mit den Schwerpunkten der traditionellen chinesischen Medizin (TCM). Da ganz besonders in der Philosophie (sogenannte 'Schule' des Wo Shen). Aber auch in der traditionellen Heilweise der TCM, wie Akupunktur, Heilkräutermedizin und weiteres.
Die Zielgruppe sind Menschen, die medizinische Hilfe benötigen. (Vom Kind bis zum älteren Menschen).
Aufgabenstellung
Es gibt ein Praxislogo, ein Foto von mir und ggf. ein Landschaftsbild. Ich dachte an fünf Hauptseiten mit Untergruppen. Am Ende sollte alles in Wordpress formatiert werden können, um es zu veröffentlichen.
Weitere Fotos zur Unterstützung der Themen kann ich natürlich gerne liefern.
Die Gestaltung ist nicht festgesetzt. Sollte aber seriös rüber kommen.

```html
<!DOCTYPE html>
<html lang="de">
<head>
<meta charset="utf-8">
<title>Naturheilpraxis Konrad Fellnroth</title>
<link rel="stylesheet" href="https://fonts.googleapis.com/css2?family=Lato:wght@300;400;700;900&display=swap">
<style>
:root{
  --gold:#d4a160;
  --gold-soft:#e2b878;
  --ink:#2b2b2b;
  --text:#3d3d3d;
  --nav:#252525;
  --line:#e3e3e3;
  --panel:#f1f1f1;
  --footer:#3c3c3c;
  --footer-text:#b9b9b9;
}
*{margin:0;padding:0;box-sizing:border-box}
html,body{width:1200px;height:2593px;overflow:hidden;background:#fff;font-family:'Lato',sans-serif;color:var(--text)}
.page{position:relative;width:1200px;height:2593px}
.abs{position:absolute}

.nav{left:0;top:0;width:1200px;height:39px;background:var(--nav);display:flex;justify-content:center}
.nav a{display:block;height:39px;line-height:38px;padding:0 24px;font-size:11.5px;font-weight:700;color:#fff;text-decoration:none;letter-spacing:.1px}
.nav a.active{background:var(--gold);color:#3a2a15}
.nav .list{display:flex;margin-left:-6px}

.hero{left:0;top:39px;width:1200px;height:430px;background:linear-gradient(180deg,#9aa7b3 0%,#b8c3c7 18%,#7f9a5a 40%,#6f9440 62%,#8aa84c 85%,#a9b870 100%)}
.hero-wave{left:0;top:380px}
.hero-logo{left:528px;top:62px;width:140px;height:140px;border-radius:50%;background:rgba(255,255,255,.35);display:flex;align-items:center;justify-content:center}
.hero-logo span{width:124px;height:124px;border-radius:50%;background:#fff;display:flex;align-items:center;justify-content:center;font-size:15px;font-weight:700;color:var(--gold)}
.hero-title{left:0;top:226px;width:1200px;text-align:center;color:#fff;font-size:42px;line-height:49px;font-weight:400;letter-spacing:.2px;text-shadow:0 1px 6px rgba(0,0,0,.25)}
.hero-title b{font-weight:900}
.hero-title .light{font-weight:300}

.h-gold{color:var(--gold);font-weight:700;letter-spacing:2.2px;text-transform:uppercase}
.about-name{left:149px;top:523px;font-size:21px}
.about-sub{left:149px;top:554px;width:470px;font-size:12.5px;line-height:15px;color:var(--ink)}
.about-rule{left:150px;top:605px;width:457px;height:1px;background:var(--line)}
.facts{left:152px;top:632px;list-style:none}
.facts li{display:flex;align-items:center;height:30px;font-size:12.8px;color:var(--ink)}
.facts svg{margin-right:16px}
.portrait-frame{left:764px;top:502px;width:285px;height:305px;border:1px solid #e1e1e1;background:#fff;box-shadow:0 14px 14px -12px rgba(0,0,0,.35)}
.portrait{left:15px;top:15px;width:254px;height:275px;background:linear-gradient(160deg,#8b8e91,#5b5f63 55%,#2a2f3a)}

.grid-line{background:var(--line)}
.cell-text h2{font-size:15.5px;margin-bottom:20px}
.cell-text p{font-size:12.8px;line-height:19.5px;color:var(--ink);margin-bottom:7px}
.what{left:149px;top:917px;width:400px}
.what-img{left:600px;top:851px;width:600px;height:375px;background:radial-gradient(circle at 40% 50%,#e7f0f6,#b6d4e4 55%,#8ebad2)}
.lab-img{left:0;top:1227px;width:601px;height:275px;background:linear-gradient(110deg,#eef0f2,#c9cdd2 40%,#e9ddd1 70%,#f3f3f3)}
.praxis{left:659px;top:1283px;width:400px}
.praxis p{line-height:22.6px}
.help{left:149px;top:1542px;width:395px}
.help .lead{font-weight:700;font-size:12.8px;line-height:19.5px;color:var(--ink);margin-bottom:22px}
.help ul{list-style:none}
.help li{display:flex;font-size:12.8px;line-height:18px;color:var(--ink);margin-bottom:12px}
.help li svg{flex:none;margin:3px 16px 0 0}
.btn-more{left:151px;top:1875px;width:128px;height:37px;background:var(--gold-soft);color:#3a2a15;font-size:12.5px;display:flex;align-items:center;justify-content:center;gap:8px}
.help-art{left:600px;top:1503px;width:598px;height:449px;background:radial-gradient(ellipse at 50% 45%,#fdf6f2,#fff 70%)}

.contact-band{left:0;top:1953px;width:1200px;height:496px;background:var(--panel)}
.contact-art{left:95px;top:1995px;width:510px;height:412px;border-radius:50% 50% 6px 6px/40% 40% 6px 6px;background:linear-gradient(180deg,#dbe4ee,#c7b590 55%,#9e8a60)}
.contact-title{left:685px;top:2030px;font-size:15.5px;color:var(--ink);letter-spacing:2.2px;font-weight:700}
.field{left:685px;width:329px;height:35px;background:#fff;border:1px solid #dcdcdc;font-size:10.5px;color:#777;padding:11px 17px}
.send{left:685px;top:2326px;width:329px;height:42px;background:var(--gold-soft);display:flex;align-items:center;justify-content:center;gap:12px;font-size:14px;font-weight:700;letter-spacing:1.2px;color:#3a2a15}

.footer{left:0;top:2449px;width:1200px;height:144px;background:var(--footer);color:var(--footer-text);font-size:11.5px;line-height:17.5px}
.foot-logo{left:154px;top:35px;width:78px;height:78px;border-radius:50%;border:1px solid #8c8c8c;display:flex;align-items:center;justify-content:center;font-size:11px;font-weight:700;color:#d8d8d8}
.foot-item{display:flex;gap:10px}
</style>
</head>
<body>
<div class="page">

  <nav class="nav abs">
    <div class="list">
      <a class="active" href="#">STARTSEITE</a>
      <a href="#">ZU MEINER PERSON</a>
      <a href="#">WOBEI KANN ICH HELFEN</a>
      <a href="#">DER ERSTE BESUCH</a>
      <a href="#">WAS IST DAS WO SHEN</a>
      <a href="#">KONTAKT</a>
    </div>
  </nav>

  <div class="hero abs" role="img" aria-label="Landschaftsfoto mit grünen Berghängen unter bewölktem Himmel"></div>
  <svg class="hero-wave abs" width="1200" height="90" viewBox="0 0 1200 90">
    <path d="M0 45 C120 10 260 -5 420 20 C600 50 760 75 920 60 C1040 50 1130 45 1200 55 L1200 90 L0 90 Z" fill="#fff"/>
  </svg>
  <div class="hero-logo abs"><span>Fellnroth</span></div>
  <h1 class="hero-title abs"><b>Naturheilpraxis</b> <span class="light">des</span><br>Heilpraktiker Konrad Fellnroth</h1>

  <h2 class="about-name abs h-gold">Konrad Fellnroth</h2>
  <p class="about-sub abs">Heilpraktiker und zertifizierter Therapeut der traditionellen chinesischen Medizin (Berufsverband BTV e.V.)</p>
  <div class="about-rule abs"></div>
  <ul class="facts abs">
    <li><svg width="22" height="22" viewBox="0 0 22 22"><path d="M19 9.5A8.5 8.5 0 1 1 14 3.2" fill="none" stroke="#333" stroke-width="1.6"/><path d="M6.5 10.5l4 4L20 4" fill="none" stroke="#d4a160" stroke-width="2"/></svg>Jahrgang 1967</li>
    <li><svg width="22" height="22" viewBox="0 0 22 22"><path d="M19 9.5A8.5 8.5 0 1 1 14 3.2" fill="none" stroke="#333" stroke-width="1.6"/><path d="M6.5 10.5l4 4L20 4" fill="none" stroke="#d4a160" stroke-width="2"/></svg>Seit 2006 Heilpraktiker in Wendenburg</li>
    <li><svg width="22" height="22" viewBox="0 0 22 22"><path d="M19 9.5A8.5 8.5 0 1 1 14 3.2" fill="none" stroke="#333" stroke-width="1.6"/><path d="M6.5 10.5l4 4L20 4" fill="none" stroke="#d4a160" stroke-width="2"/></svg>Seit 2010 Gründer und Leiter des VKL Blutanalyselabors in Wendenburg</li>
    <li><svg width="22" height="22" viewBox="0 0 22 22"><path d="M19 9.5A8.5 8.5 0 1 1 14 3.2" fill="none" stroke="#333" stroke-width="1.6"/><path d="M6.5 10.5l4 4L20 4" fill="none" stroke="#d4a160" stroke-width="2"/></svg>Seit 2015 zertifizierter TCM Therapeut (Berufsverband BTV e.V.)</li>
    <li><svg width="22" height="22" viewBox="0 0 22 22"><path d="M19 9.5A8.5 8.5 0 1 1 14 3.2" fill="none" stroke="#333" stroke-width="1.6"/><path d="M6.5 10.5l4 4L20 4" fill="none" stroke="#d4a160" stroke-width="2"/></svg>Beschäftigung mit der Wo Shen Philosophie (Schule) seit 1988</li>
  </ul>
  <div class="portrait-frame abs">
    <div class="portrait abs" role="img" aria-label="Porträtfoto des Heilpraktikers"></div>
  </div>

  <div class="grid-line abs" style="left:0;top:850px;width:1200px;height:1px"></div>
  <div class="grid-line abs" style="left:0;top:1226px;width:1200px;height:1px"></div>
  <div class="grid-line abs" style="left:0;top:1502px;width:1200px;height:1px"></div>
  <div class="grid-line abs" style="left:0;top:850px;width:1px;height:1103px"></div>
  <div class="grid-line abs" style="left:1199px;top:850px;width:1px;height:1103px"></div>
  <div class="grid-line abs" style="left:600px;top:1502px;width:1px;height:451px"></div>

  <div class="what cell-text abs">
    <h2 class="h-gold">Was mache ich</h2>
    <p>Seit vielen Jahrzehnten begeistere ich mich für die Themen der Medizin und die Wiederherstellung der Gesundheit.</p>
    <p>Ein grundlegendes Gesundheitssystem habe ich schon immer in der traditionellen chinesischen Medizin gesehen.</p>
    <p>Die traditionelle chinesische Medizin ist eine der ältesten Heilkunde- und Therapieform der Welt. Unzählige Therapierichtungen, sogenannte „Schulen“, sind im Laufe der vergangenen Jahrtausende entstanden.</p>
    <p>Eine dieser Richtungen ist die Schule des „Wo Shen“. Diese besteht aus philosophischen Betrachtungen, Erklärungsformen und konkreten Therapieformen.</p>
  </div>
  <div class="what-img abs" role="img" aria-label="Foto einer Hand mit Kapsel, umgeben von leuchtenden Medizin-Symbolen"></div>

  <div class="lab-img abs" role="img" aria-label="Foto eines Mikroskops mit Blutprobe auf einem Objektträger"></div>
  <div class="praxis cell-text abs">
    <h2 class="h-gold">Die Praxis</h2>
    <p>Seit 2012 besteht die Praxis, in der sich auch das VKL Blutanalyselabor befindet, im dritten Stock eines Wohn- und Geschäftshauses in der Wendenburger Innenstadt. Ein Aufzug ist vorhanden. Die Praxis ist gut mit öffentlichen Verkehrsmitteln zu erreichen und hat in unmittelbarer Nähe auch ein Parkhaus. (Tiefgarage und Haltstelle Lindenhof)</p>
  </div>

  <div class="help cell-text abs">
    <h2 class="h-gold" style="margin-bottom:14px">Wobei kann ich helfen</h2>
    <p class="lead">Der Schwerpunkt meiner Tätigkeit ist die Beseitigung und Linderung von chronischen Erkrankungen und deren Folgen. Hierzu zählen u.a.:</p>
    <ul>
      <li><svg width="14" height="12" viewBox="0 0 14 12"><path d="M1 6l4 4L13 1" fill="none" stroke="#d4a160" stroke-width="1.8"/></svg>Der rheumatische Formenkreis / Erkrankungen die mit Entzündungen und Schmerzzuständen einhergehen</li>
      <li><svg width="14" height="12" viewBox="0 0 14 12"><path d="M1 6l4 4L13 1" fill="none" stroke="#d4a160" stroke-width="1.8"/></svg>Magen- und Darmbeschwerden / Unverträglichkeiten bis hin zu allergischen Dispositionen</li>
      <li><svg width="14" height="12" viewBox="0 0 14 12"><path d="M1 6l4 4L13 1" fill="none" stroke="#d4a160" stroke-width="1.8"/></svg>Diabetes / Stoffwechselstörungen</li>
      <li><svg width="14" height="12" viewBox="0 0 14 12"><path d="M1 6l4 4L13 1" fill="none" stroke="#d4a160" stroke-width="1.8"/></svg>Chronische virale- und bakterielle Belastungen</li>
      <li><svg width="14" height="12" viewBox="0 0 14 12"><path d="M1 6l4 4L13 1" fill="none" stroke="#d4a160" stroke-width="1.8"/></svg>Belastungen psychischer Natur / Erschöpfungszustände</li>
      <li><svg width="14" height="12" viewBox="0 0 14 12"><path d="M1 6l4 4L13 1" fill="none" stroke="#d4a160" stroke-width="1.8"/></svg>Long Covid Belastungen</li>
    </ul>
  </div>
  <div class="btn-more abs">
    <svg width="12" height="8" viewBox="0 0 12 8"><path d="M0 4h11M8 1l3 3-3 3" fill="none" stroke="#3a2a15" stroke-width="1.2"/></svg>Lern mehr
  </div>
  <div class="help-art abs" role="img" aria-label="Illustration mit medizinischen Symbolen im Halbkreis um das Praxissymbol, seitlich dezente Icon-Muster"></div>

  <div class="contact-band abs"></div>
  <div class="contact-art abs" role="img" aria-label="Illustration: drei Personen rund um einen großen Briefumschlag, Thema Kontakt"></div>
  <h2 class="contact-title abs">SCHNELLER KONTAKT</h2>
  <div class="field abs" style="top:2071px">Vollständiger Name</div>
  <div class="field abs" style="top:2113px">Email</div>
  <div class="field abs" style="top:2155px">Telefon</div>
  <div class="field abs" style="top:2197px;height:120px">Ihre Anfrage</div>
  <div class="send abs">
    <svg width="18" height="16" viewBox="0 0 18 16"><path d="M1 9L17 1 12 15 8 10Z M8 10L17 1" fill="none" stroke="#3a2a15" stroke-width="1.1"/></svg>SENDEN
  </div>

  <footer class="footer abs">
    <div class="foot-logo abs">Fellnroth</div>
    <div class="foot-item abs" style="left:342px;top:46px">
      <svg width="14" height="16" viewBox="0 0 14 16"><path d="M7 15s5-5.5 5-9A5 5 0 0 0 2 6c0 3.5 5 9 5 9z" fill="#d4a160"/><circle cx="7" cy="6" r="2" fill="#3c3c3c"/></svg>
      <div>Konrad Fellnroth<br>Lindenweg 12<br>47293 Wendenburg</div>
    </div>
    <div class="foot-item abs" style="left:599px;top:46px">
      <svg width="14" height="14" viewBox="0 0 14 14"><path d="M3 1l2 3-1.3 1.5a8 8 0 0 0 4.8 4.8L10 9l3 2-1.3 2.3C6 13 1 8 .7 2.3Z" fill="none" stroke="#d4a160" stroke-width="1.1"/></svg>
      <div>Telefon 0555 – 418 27 60</div>
    </div>
    <div class="foot-item abs" style="left:599px;top:72px">
      <svg width="15" height="12" viewBox="0 0 15 12"><rect x=".6" y=".6" width="13.8" height="10.8" fill="none" stroke="#d4a160" stroke-width="1.1"/><path d="M.6.6l6.9 6 6.9-6" fill="none" stroke="#d4a160" stroke-width="1.1"/></svg>
      <div>Post@heilpraktiker-fellnroth.de</div>
    </div>
    <div class="abs" style="left:932px;top:46px;line-height:22px">Impressum<br>Datenschutzerklärung</div>
  </footer>

</div>
</body>
</html>
```